Nutrition business needs logo & business card design

We need a business card & logo design for a new company based in Toronto, Ontario Canada called Verdel Wellworks.

We provide nutrition service using metrics as guide to manage client's progress. Our service creates individualized nutrition and lifestyle strategies that focuses on improving Performance, Longevity and Weight Loss. I would like to see designs that use the color of green, gray, blue and white.

The final design should:

--convey a feeling of connectedness with positive transformation.

-- communicate the idea of awareness with guided effort that yields personal independence for a better and more productive life

Target Market(s)

Professionals who work in the IT/Computer/Engineering/Banking industry specifically Directors, Managers, CEO's.

Industry/Entity Type

Health And Wellness

Contact Information for Business Card

Dorvane Pike, Owner
email: DPIKE@verdelwellworks.example
tel: - 555-204-7718

Logo Text

better health through analytics or measure to manage

Font styles to use
Other font styles liked:
• Garamound

Colors
ffffff
abd037
85acd3
757575
34a7d7

Requirements
Must have
• Good contrast and decent size font - ease of readability, aesthetically nice colors
Nice to have
• image of chart or graph that conveys measurement or analytics
Should not have
• Borders, images of food,

```html
<!DOCTYPE html>
<html lang="en">
<head>
<meta charset="utf-8">
<title>Verdel Wellworks – Business Cards</title>
<link href="https://fonts.googleapis.com/css2?family=Oswald:wght@300&family=Open+Sans:wght@400;700&display=swap" rel="stylesheet">
<style>
  :root {
    --backdrop: #ecebe8;
    --card-white: #ffffff;
    --green-top: #66b23b;
    --green-bottom: #12672b;
    --brand-green: #2f8f36;
    --ink-light: #ffffff;
    --shadow: rgba(0, 0, 0, 0.18);
  }
  html, body {
    margin: 0;
    padding: 0;
    width: 1200px;
    height: 900px;
    overflow: hidden;
    background: var(--backdrop);
  }
  .canvas {
    position: relative;
    width: 1200px;
    height: 900px;
  }
  .card {
    position: absolute;
    box-shadow: 0 6px 18px var(--shadow);
    overflow: hidden;
  }
  .card--front {
    left: 238px;
    top: 62px;
    width: 555px;
    height: 343px;
    background: linear-gradient(to bottom, var(--green-top), var(--green-bottom));
    color: var(--ink-light);
  }
  .card--back {
    left: 457px;
    top: 518px;
    width: 560px;
    height: 344px;
    background: var(--card-white);
  }
  .brand-mark {
    position: absolute;
    border-radius: 50%;
    box-sizing: border-box;
  }
  .card--front .brand-mark {
    left: 245px;
    top: 40px;
    width: 64px;
    height: 64px;
    border: 3px solid var(--ink-light);
  }
  .card--back .brand-mark {
    left: 246px;
    top: 92px;
    width: 68px;
    height: 68px;
    border: 3px solid var(--brand-green);
  }
  .brand-name {
    position: absolute;
    left: 0;
    right: 0;
    margin: 0;
    text-align: center;
    font-family: "Oswald", sans-serif;
    font-weight: 300;
    line-height: 1;
    white-space: nowrap;
  }
  .card--front .brand-name {
    top: 128px;
    font-size: 44px;
  }
  .card--back .brand-name {
    top: 206px;
    font-size: 52px;
    color: var(--brand-green);
  }
  .person {
    position: absolute;
    right: 288px;
    top: 200px;
    text-align: right;
    font-family: "Open Sans", sans-serif;
    font-size: 14px;
    line-height: 20px;
    white-space: nowrap;
  }
  .person__name {
    margin: 0;
    font-size: 20px;
    font-weight: 700;
    line-height: 26px;
  }
  .person__role { margin: 0 0 16px; }
  .person__address { margin: 0; font-style: normal; }
  .contact-list {
    position: absolute;
    left: 286px;
    top: 204px;
    margin: 0;
    padding: 0;
    list-style: none;
    font-family: "Open Sans", sans-serif;
    font-size: 14px;
    line-height: 20px;
    white-space: nowrap;
  }
  .contact-list li {
    display: flex;
    align-items: center;
    gap: 6px;
  }
  .contact-icon {
    width: 10px;
    height: 10px;
    flex: none;
    fill: var(--ink-light);
    stroke: var(--ink-light);
  }
</style>
</head>
<body>
<main class="canvas">
  <section class="card card--front">
    <span class="brand-mark" aria-hidden="true"></span>
    <h1 class="brand-name">Verdel Wellworks</h1>

    <div class="person">
      <p class="person__name">Dorvane Pike</p>
      <p class="person__role">Owner</p>
      <address class="person__address">1234, Address Goes Here<br>Country Name, 123456</address>
    </div>

    <ul class="contact-list">
      <li>
        <svg class="contact-icon" viewBox="0 0 10 10" aria-hidden="true"><rect x="2.5" y="0.5" width="5" height="9" rx="1" fill="none" stroke-width="1.2"/><rect x="4" y="7.3" width="2" height="1" stroke="none"/></svg>
        <span>555-204-7718</span>
      </li>
      <li>
        <svg class="contact-icon" viewBox="0 0 10 10" aria-hidden="true"><path d="M0.5 3.5 Q5 0 9.5 3.5 L8 4.5 L6.5 3.5 L3.5 3.5 L2 4.5 Z" stroke="none"/><rect x="2" y="5" width="6" height="4.5" rx="0.8" stroke="none"/></svg>
        <span>555-204-7718</span>
      </li>
      <li>
        <svg class="contact-icon" viewBox="0 0 10 10" aria-hidden="true"><rect x="2.5" y="0.5" width="5" height="3" fill="none" stroke-width="1"/><rect x="0.5" y="3.5" width="9" height="6" rx="0.8" stroke="none"/></svg>
        <span>555-204-7718</span>
      </li>
      <li>
        <svg class="contact-icon" viewBox="0 0 10 10" aria-hidden="true"><rect x="0.5" y="2" width="9" height="6.5" stroke="none"/><path d="M0.8 2.3 L5 5.6 L9.2 2.3" fill="none" stroke="#1f7a30" stroke-width="1"/></svg>
        <span>DPIKE@verdelwellworks.example</span>
      </li>
      <li>
        <svg class="contact-icon" viewBox="0 0 10 10" aria-hidden="true"><path d="M4 6 L6 4 M3.3 4.7 L1.8 6.2 a1.5 1.5 0 0 0 2 2 L5.3 6.7 M4.7 3.3 L6.2 1.8 a1.5 1.5 0 0 1 2 2 L6.7 5.3" fill="none" stroke-width="1.2" stroke-linecap="round"/></svg>
        <span>www.verdelwellworks.example</span>
      </li>
    </ul>
  </section>

  <section class="card card--back">
    <span class="brand-mark" aria-hidden="true"></span>
    <h2 class="brand-name">Verdel Wellworks</h2>
  </section>
</main>
</body>
</html>
```